Movie Poster - Beneath Pale Iron Skies

Documentary-film poster design.
Attached is a PDF brief with information on what is required and examples of poster designs I like.

The project is a true crime / mystery documentary film. Set in the Soviet Union in 1959.

Colors
3276b5
85abd2
ec1f27

```html
<!DOCTYPE html>
<html lang="en">
<head>
<meta charset="UTF-8">
<title>Beneath Pale Iron Skies — Documentary Poster</title>
<link rel="stylesheet" href="https://fonts.googleapis.com/css2?family=Bebas+Neue&family=Oswald:wght@600;700&display=swap">
<style>
  :root {
    --snow: #d9e3e2;
    --snow-deep: #b9c9c8;
    --rock: #3c4c4d;
    --rock-dark: #243031;
    --ink: #111616;
    --blood: #6b0b0f;
    --paper: #f2f5f4;
    --frame: #0b0d0d;
  }
  * { margin: 0; padding: 0; box-sizing: border-box; }
  html, body { width: 800px; height: 1200px; overflow: hidden; background: var(--snow); }
  .poster { position: relative; width: 800px; height: 1200px; overflow: hidden; }

  .backdrop {
    position: absolute; inset: 0;
    background:
      radial-gradient(ellipse 190px 330px at 90px 230px, var(--rock-dark) 0%, var(--rock) 55%, transparent 100%),
      radial-gradient(ellipse 230px 260px at 100px 700px, var(--rock) 0%, rgba(60,76,77,0.6) 55%, transparent 100%),
      radial-gradient(ellipse 420px 150px at 620px 700px, rgba(90,110,110,0.55) 0%, transparent 100%),
      linear-gradient(180deg, #cfdbda 0%, var(--snow) 45%, #e3eaea 80%, var(--snow-deep) 100%);
  }

  .title {
    position: absolute; left: 80px; top: 78px; width: 640px;
    font-family: "Bebas Neue", "Oswald", sans-serif;
    color: var(--ink); text-transform: uppercase;
    font-size: 126px; line-height: 0.98; letter-spacing: 1px;
    text-align: center;
  }

  .filmstrip {
    position: absolute; left: 0; top: 343px; width: 800px; height: 135px;
    background: var(--frame); display: flex; gap: 4px; padding: 4px;
  }
  .still { flex: 1; background: linear-gradient(180deg, #bcc7c6 0%, #5d6868 60%, #2c3333 100%); }
  .still--forest { background: linear-gradient(180deg, #3a4443 0%, #6f7a78 60%, #2a302f 100%); }

  .tagline {
    position: absolute; left: 80px; top: 504px; width: 634px;
    font-family: "Oswald", sans-serif; font-weight: 700;
    font-size: 34px; letter-spacing: -0.5px; color: var(--ink);
    text-transform: uppercase; text-align: center; white-space: nowrap;
  }

  .figures { position: absolute; left: 0; top: 590px; width: 800px; height: 290px; }

  .mystery {
    position: absolute; left: 100px; top: 904px; width: 590px;
    font-family: "Oswald", sans-serif; font-weight: 700;
    font-size: 40px; letter-spacing: -0.5px; color: #222a2a;
    text-transform: uppercase; text-align: center; white-space: nowrap;
  }
  .reveal {
    position: absolute; left: 196px; top: 930px; width: 500px;
    font-family: "Bebas Neue", sans-serif;
    font-size: 104px; line-height: 1; letter-spacing: 1px;
    color: var(--blood); text-transform: uppercase; text-align: center;
  }
</style>
</head>
<body>
<main class="poster">
  <div class="backdrop" role="img" aria-label="Snowy mountain pass with a dark rock outcrop on the left and forested slopes behind"></div>

  <h1 class="title">Beneath Pale<br>Iron Skies</h1>

  <div class="filmstrip">
    <div class="still" role="img" aria-label="Expedition group riding in the back of a truck"></div>
    <div class="still" role="img" aria-label="Two hikers embracing outside a cabin"></div>
    <div class="still" role="img" aria-label="Skiers crossing a snowfield"></div>
    <div class="still" role="img" aria-label="Group of hikers gathered on the trail"></div>
    <div class="still" role="img" aria-label="Skiers walking into a blizzard"></div>
    <div class="still still--forest" role="img" aria-label="Memorial obelisk among trees"></div>
  </div>

  <p class="tagline">The true story of the Kholvar Pass incident</p>

  <svg class="figures" viewBox="0 0 800 290" aria-label="9 dead hikers, 60 years of secrets">
    <g font-family="Bebas Neue, sans-serif" fill="#6b0b0f" opacity="0.92">
      <text x="183" y="274" font-size="372" text-anchor="middle">9</text>
      <text x="520" y="274" font-size="372" text-anchor="middle" letter-spacing="24">60</text>
    </g>
    <text transform="translate(262 250) rotate(-90)" font-family="Oswald, sans-serif" font-weight="700" font-size="36" fill="#f2f5f4" textLength="228" lengthAdjust="spacingAndGlyphs">DEAD HIKERS</text>
    <g font-family="Oswald, sans-serif" font-weight="700" font-size="34" fill="#f2f5f4">
      <text x="354" y="266" textLength="154" lengthAdjust="spacingAndGlyphs">YEARS OF</text>
      <text x="540" y="266" textLength="142" lengthAdjust="spacingAndGlyphs">SECRETS</text>
    </g>
  </svg>

  <p class="mystery">Russia`s greatest mystery</p>
  <p class="reveal">Uncovered.</p>
</main>
</body>
</html>
```